Brellwick Partners, LLC Stationary

Brellwick Partners, LLC is a new financial planning and consulting company. We are looking for designs on business cards, letterhead, envelopes, and anything else that would be useful. Our preference for business card design is two sided. We are looking for a professional and clean look with incorporating the logo and patriotic feel. Thank you to all who participate and good luck!

```html
<!DOCTYPE html>
<html lang="en">
<head>
<meta charset="utf-8">
<title>Brellwick Partners, LLC – Business Card</title>
<link rel="stylesheet" href="https://fonts.googleapis.com/css2?family=Questrial&display=swap">
<style>
  :root {
    --page-bg: #d8d5d0;
    --navy-deep: #0f1d33;
    --navy: #1d3253;
    --navy-mid: #2b4266;
    --red: #b01e23;
    --red-bright: #c8262b;
    --frost: #eceef0;
    --frost-shade: #dcdfe3;
    --text-light: #d6dbe3;
    --text-soft: #b8c0cc;
    --brand-navy: #1b2a47;
  }
  * { box-sizing: border-box; margin: 0; padding: 0; }
  html, body {
    width: 1200px;
    height: 969px;
    overflow: hidden;
    background: var(--page-bg);
    font-family: "Questrial", "Helvetica Neue", Arial, sans-serif;
  }
  .canvas {
    position: relative;
    width: 1200px;
    height: 969px;
  }
  .card {
    position: absolute;
    left: 100px;
    top: 200px;
    width: 1000px;
    height: 569px;
    overflow: hidden;
    background: linear-gradient(160deg, var(--frost) 0%, var(--frost-shade) 100%);
    box-shadow: 0 18px 40px rgba(0, 0, 0, 0.22);
  }
  .card-shapes {
    position: absolute;
    inset: 0;
  }
  .holder {
    position: absolute;
    left: 43px;
    top: 60px;
  }
  .holder-name {
    color: var(--red-bright);
    font-size: 30px;
    letter-spacing: 1.5px;
    line-height: 1.1;
    text-transform: uppercase;
  }
  .holder-role {
    color: var(--text-light);
    font-size: 26px;
    letter-spacing: 1.2px;
    margin-top: 4px;
    text-transform: uppercase;
  }
  .address {
    position: absolute;
    left: 43px;
    top: 274px;
    color: var(--text-light);
    font-size: 26px;
    line-height: 1.38;
  }
  .contacts {
    position: absolute;
    left: 43px;
    top: 370px;
    list-style: none;
  }
  .contacts li {
    display: flex;
    align-items: center;
    height: 39.5px;
    color: var(--text-soft);
    font-size: 24px;
  }
  .contacts svg {
    width: 24px;
    height: 24px;
    margin-right: 20px;
    flex: none;
  }
  .brand {
    position: absolute;
    left: 460px;
    width: 540px;
    top: 255px;
    text-align: center;
    color: var(--brand-navy);
    font-size: 38px;
    letter-spacing: 1px;
    line-height: 1.2;
  }
</style>
</head>
<body>
<main class="canvas">
  <section class="card" aria-label="Business card front">
    <svg class="card-shapes" viewBox="0 0 1000 569" width="1000" height="569" aria-hidden="true">
      <defs>
        <linearGradient id="panelShade" x1="0" y1="0" x2="1" y2="0.3">
          <stop offset="0" stop-color="var(--navy-deep)"/>
          <stop offset="0.55" stop-color="var(--navy)"/>
          <stop offset="1" stop-color="var(--navy-mid)"/>
        </linearGradient>
      </defs>
      <polygon class="dark-panel" points="0,0 628,0 412,284 628,569 0,569" fill="url(#panelShade)"/>
      <polygon class="red-accent" points="606,34 612,34 420,284 612,535 606,535 407,284" fill="var(--red)"/>
    </svg>

    <div class="holder">
      <p class="holder-name">Elliot Marrow</p>
      <p class="holder-role">CEO/Founder</p>
    </div>

    <address class="address" style="font-style: normal;">
      4120 Linden Court<br>
      Fairbrook, Oregon 97215
    </address>

    <ul class="contacts">
      <li>
        <svg viewBox="0 0 24 24" aria-hidden="true"><path fill="var(--red-bright)" d="M6.6 10.8a15.2 15.2 0 0 0 6.6 6.6l2.2-2.2a1 1 0 0 1 1-.25 11.4 11.4 0 0 0 3.6.57 1 1 0 0 1 1 1V20a1 1 0 0 1-1 1A17 17 0 0 1 3 4a1 1 0 0 1 1-1h3.5a1 1 0 0 1 1 1c0 1.25.2 2.45.57 3.6a1 1 0 0 1-.25 1z"/></svg>
        555 214 7390
      </li>
      <li>
        <svg viewBox="0 0 24 24" aria-hidden="true"><path fill="var(--red-bright)" d="M6 3h12v5H6zM3 9h18a1 1 0 0 1 1 1v7h-4v4H6v-4H2v-7a1 1 0 0 1 1-1zm5 6v4h8v-4z"/></svg>
        555 803 1462
      </li>
      <li>
        <svg viewBox="0 0 24 24" aria-hidden="true"><path fill="var(--red-bright)" d="M2 5h20v14H2zm2 2v.5l8 5 8-5V7zm0 2.8V17h16V9.8l-8 5z"/></svg>
        hello@brellwick.com
      </li>
      <li>
        <svg viewBox="0 0 24 24" aria-hidden="true"><circle cx="12" cy="12" r="9" fill="none" stroke="var(--red-bright)" stroke-width="2"/><path fill="none" stroke="var(--red-bright)" stroke-width="1.6" d="M3 12h18M12 3c3 3 3 15 0 18M12 3c-3 3-3 15 0 18"/></svg>
        www.brellwick.com
      </li>
    </ul>

    <p class="brand">Brellwick Partners, LLC</p>
  </section>
</main>
</body>
</html>
```